Stonebrace Business Card Design

The Stonebrace Co is an aggregate (crushing) equipment dealer serving Western Canadian provinces. Stonebrace is a distributor of aggregate equipment for different manufacturers.

We are looking to change and update the existing business card which has been used since the existence of the company. A copy of existing card has been attached for reference. The Stonebrace Co logo we want to remain the same and we want the green color to remain the same.

We are wanting something new with a different look. A refreshing card to show a new modern and updated look. No longer wanting to have the manufacturers on the back of the card but something more like our logo on the back of the card with a statement like "Crushing Solutions"

ideas could be:
- card can be different colors on front and back
- front or reverse of the card could possibly be the green color with the logo in black

Target Market(s)

Owners of Aggregate/Crushing companies

Contact Information for Business Card

see above

Requirements
Must have
• - logo to remain same along with same font within logo
• - green color to remain same
Nice to have
• as noted above under project description
Should not have

```html
<!DOCTYPE html>
<html lang="en">
<head>
<meta charset="utf-8">
<title>Stonebrace Business Card</title>
<link href="https://fonts.googleapis.com/css2?family=Roboto:wght@400;500;700&family=Roboto+Condensed:wght@400;700&display=swap" rel="stylesheet">
<style>
  :root {
    --brand-green: #878b0c;
    --brand-green-dark: #74780a;
    --ink: #222222;
    --paper: #f4f4f4;
    --white: #ffffff;
    --backdrop: #e6e3de;
  }
  html, body {
    margin: 0;
    width: 1200px;
    height: 960px;
    overflow: hidden;
    background: var(--backdrop);
  }
  .stage {
    position: relative;
    width: 1200px;
    height: 960px;
  }
  .card {
    position: absolute;
    left: 320px;
    width: 600px;
    border-radius: 18px;
    overflow: hidden;
    box-shadow: 0 3px 8px rgba(0,0,0,0.25);
  }

  /* Back side */
  .card-back {
    top: 110px;
    height: 336px;
    background: var(--brand-green);
  }
  .back-brand {
    position: absolute;
    right: 32px;
    top: 270px;
    text-align: right;
    color: var(--ink);
    font-family: "Roboto", Arial, sans-serif;
  }
  .back-brand .company {
    font-weight: 700;
    font-size: 20px;
    letter-spacing: 0.2px;
    margin: 0;
  }
  .back-brand .tagline {
    font-weight: 700;
    font-size: 14px;
    margin: 4px 46px 0 0;
  }

  /* Front side */
  .card-front {
    top: 493px;
    height: 342px;
    background: var(--paper);
  }
  .front-wave {
    position: absolute;
    inset: 0;
    width: 600px;
    height: 342px;
  }
  .front-company {
    position: absolute;
    left: 36px;
    top: 152px;
    margin: 0;
    font-family: "Roboto", Arial, sans-serif;
    font-weight: 700;
    font-size: 20px;
    color: var(--ink);
    letter-spacing: 0.2px;
  }
  .contact {
    position: absolute;
    right: 24px;
    top: 146px;
    text-align: right;
    color: var(--white);
    font-family: "Roboto", Arial, sans-serif;
  }
  .contact .person-name {
    margin: 0;
    font-family: "Roboto Condensed", Arial, sans-serif;
    font-weight: 700;
    font-size: 22px;
    line-height: 26px;
  }
  .contact .person-title {
    margin: 0 0 16px;
    font-family: "Roboto Condensed", Arial, sans-serif;
    font-size: 16px;
    line-height: 20px;
  }
  .contact-list {
    list-style: none;
    margin: 0;
    padding: 0;
    font-size: 14px;
    line-height: 19.5px;
  }
  .contact-list li {
    display: flex;
    justify-content: flex-end;
    align-items: center;
    gap: 8px;
  }
  .contact-list svg {
    width: 12px;
    height: 12px;
    fill: var(--white);
  }
  .contact-list .address {
    margin-top: 3px;
  }
</style>
</head>
<body>
<main class="stage">

  <section class="card card-back" aria-label="Card back">
    <div class="back-brand">
      <p class="company">THE STONEBRACE CO.</p>
      <p class="tagline">Crushing Solutions</p>
    </div>
  </section>

  <section class="card card-front" aria-label="Card front">
    <svg class="front-wave" viewBox="0 0 600 342" aria-hidden="true">
      <path fill="var(--brand-green)" d="M0,268 C150,300 265,300 350,205 C430,115 510,76 600,74 L600,342 L0,342 Z"/>
      <path fill="var(--white)" d="M0,270 C150,305 262,302 352,210 C432,125 515,88 600,90 L600,96 C520,96 445,132 368,215 C280,312 140,322 0,306 Z"/>
    </svg>

    <p class="front-company">THE STONEBRACE CO.</p>

    <div class="contact">
      <p class="person-name">DALE MORROW</p>
      <p class="person-title">CEO/FOUNDER</p>
      <ul class="contact-list">
        <li>780.555.0142
          <svg viewBox="0 0 12 12"><path d="M2.4 0.6 L4.2 0.4 L5 3 L3.7 4 C4.4 5.6 5.8 7 7.4 7.8 L8.4 6.5 L11 7.3 L10.8 9.2 C10.6 10.6 9.6 11.4 8 11 C4.4 10 1.6 7.2 0.6 3.6 C0.3 2.2 1 1 2.4 0.6 Z"/></svg>
        </li>
        <li>780.555.0187
          <svg viewBox="0 0 12 12"><path d="M3 0 H9 A1 1 0 0 1 10 1 V11 A1 1 0 0 1 9 12 H3 A1 1 0 0 1 2 11 V1 A1 1 0 0 1 3 0 Z M3.3 1.4 V9.6 H8.7 V1.4 Z M5.3 10.3 H6.7 V11.2 H5.3 Z"/></svg>
        </li>
        <li>780.555.0163
          <svg viewBox="0 0 12 12"><path d="M3 0.5 H9 V3.5 H3 Z M0.5 4.5 H11.5 V9.5 H9.5 V11.5 H2.5 V9.5 H0.5 Z M3.5 8 V10.3 H8.5 V8 Z"/></svg>
        </li>
        <li>dale@stonebr.com
          <svg viewBox="0 0 12 12"><path d="M0.5 2.5 H11.5 V3.2 L6 6.6 L0.5 3.2 Z M0.5 4.4 L6 7.8 L11.5 4.4 V9.5 H0.5 Z"/></svg>
        </li>
        <li>www.stonebrace.ca
          <svg viewBox="0 0 12 12"><path d="M6 0.5 A5.5 5.5 0 1 0 6 11.5 A5.5 5.5 0 1 0 6 0.5 Z M3.4 3 C4.6 3.4 4.2 4.6 5.4 5 C6.4 5.3 6 6.8 7 7.4 C7.6 7.8 7.4 9 6.6 9.8 C5.4 9.4 5 8.4 4.4 7.6 C3.6 6.8 2.6 6.2 2 5 C2.3 4.2 2.8 3.5 3.4 3 Z M7.4 2.2 C8.6 2.6 9.6 3.6 10 4.8 C9.2 5 8.4 4.4 7.8 3.8 C7.4 3.4 7.2 2.8 7.4 2.2 Z"/></svg>
        </li>
        <li class="address">2210- 48B Avenue, Nisku, Alberta T9E 1K7</li>
      </ul>
    </div>
  </section>

</main>
</body>
</html>
```